Distribution/Printing company needs a web site to inform prospective customers on what we do.

Distribution/Printing/Packaging company needs a web site to inform prospective customers on what we do. Please look at our direct to consumer web site (under development) for an idea of the product lines we sell: storedev.maplewickhaven.com
Logo files are attached as is a flyer that is under development which contains other information about the company (this is to be used for content- not to be posted as is). The web site should be focused on our business customer base and is not intended to be direct to consumer. Site should have a link to our consumer web site.
Site design should be mobile friendly, or mobile could be redirected to a mobile version. This web site will be strictly informational and will not be designed for any sales transactions.

Target Market(s)

Manufacturing and retail businesses, any other multi-site business that would benefit from centralized pricing and budget controls we can provide (banks, medical/dental offices, educational facilities, etc).

Industry/Entity Type

It Company

Coding

Coded - Design and coding required

Number of Pages Required

5+ page

Requirements
Must have
• 1) Top level menu: Products, about us, locations, contact us, news
• 2) page with news/promotions that is easily updated
• 3) "contact us" form (name, company, phone, email address) email link
• 4) link to www.store.maplewickhaven.com with information that lower pricing is available for businesses
• 5) SEO keywords
• 6) Link to powerpoint presentation file
Nice to have
• 1) our phone number should appear on every page near the top

```html
<!DOCTYPE html>
<html lang="en">
<head>
<meta charset="utf-8">
<title>Maplewick Haven Supply — Packaging, Printing, Distribution</title>
<meta name="keywords" content="packaging, printing, distribution, business supply, centralized pricing, budget controls">
<link rel="stylesheet" href="https://fonts.googleapis.com/css2?family=Ubuntu:wght@300;400;500;700&display=swap">
<style>
  :root{
    --page-bg:#e8e8e2;
    --panel:#ffffff;
    --panel-edge:#dcdcd6;
    --ink:#2b2b2b;
    --body-text:#4a4a4a;
    --muted:#6d6d6d;
    --link:#1a8fcf;
    --nav-tab:#f3f3f0;
    --nav-active:#fbfbf9;
    --news-bg:#f1f1ee;
    --rule:#b9b9b4;
    --btn:#4a4a4a;
    --green-top:#a4e04a;
    --green-bottom:#5fb21a;
    --col-title:#1c5fa8;
  }
  *{box-sizing:border-box;margin:0;padding:0}
  html,body{width:1200px;height:1023px;overflow:hidden}
  body{
    position:relative;
    background:var(--page-bg);
    font-family:"Ubuntu",sans-serif;
    color:var(--ink);
  }
  a{text-decoration:none;color:inherit}

  .brand{position:absolute;left:134px;top:78px;white-space:nowrap}
  .brand-name{display:flex;align-items:center;gap:7px;font-size:17px;font-weight:700;color:#333;letter-spacing:.2px}
  .brand-name .mark{width:11px;height:11px;background:#333}
  .brand-tagline{margin-top:3px;font-size:12.5px;font-weight:500;color:#444}

  .main-nav{position:absolute;left:411px;top:80px;height:56px}
  .main-nav a{
    position:absolute;bottom:0;height:45px;width:103px;
    background:linear-gradient(#fafaf8,var(--nav-tab));
    border:1px solid var(--panel-edge);border-bottom:none;
    border-radius:12px 12px 0 0;
    font-size:13px;font-weight:500;color:#222;
    display:flex;align-items:center;justify-content:center;padding-top:4px;
  }
  .main-nav a.active{height:56px;background:var(--nav-active);padding-top:0;padding-bottom:10px}

  .panel{
    position:absolute;left:115px;top:136px;width:972px;height:845px;
    background:linear-gradient(#fbfbfa,#ffffff 40%);
    border:1px solid var(--panel-edge);border-radius:12px;
    box-shadow:0 0 6px rgba(0,0,0,.05);
  }
  .hero{
    position:absolute;left:13px;top:15px;width:947px;height:306px;
    border-radius:10px;border:2px solid #d8d8d2;
    background:radial-gradient(ellipse at 55% 60%,#6b5140 0%,#8a6a50 18%,#d9d6cf 45%,#ececea 70%);
  }

  .section-title{position:absolute;display:flex;align-items:center;gap:8px;font-weight:300;color:#222;white-space:nowrap}
  .welcome-title{left:22px;top:355px;font-size:29px}
  .welcome-title strong{font-weight:400}
  .services-title{left:22px;top:590px;font-size:29px}
  .icon{width:32px;height:34px}

  .welcome-photo{position:absolute;left:14px;top:413px;width:194px;height:131px;background:linear-gradient(135deg,#e9e5de,#cdb08b 55%,#efece7)}
  .welcome-text{position:absolute;left:216px;top:421px;width:426px;font-size:11.3px;line-height:16px;color:var(--body-text)}
  .welcome-text .lead{color:var(--link)}
  .read-more{display:block;margin-top:4px;font-size:11.5px;font-weight:500;color:var(--link)}

  .services-rule{position:absolute;left:22px;top:633px;width:619px;height:1px;background:var(--rule)}
  .service{position:absolute;top:646px;width:188px}
  .service + .service{border-left:1px solid #e3e3e0}
  .service h3{text-align:center;font-size:13px;font-weight:400;color:var(--col-title);height:26px}
  .service .photo{height:63px}
  .service p{margin-top:9px;padding-left:5px;font-size:11.3px;line-height:16px;color:var(--body-text)}
  .service .btn{display:inline-block;margin:6px 0 0 5px;width:67px;height:23px;line-height:23px;text-align:center;background:var(--btn);color:#fff;font-size:11px;border-radius:3px}

  .news{
    position:absolute;left:666px;top:355px;width:279px;height:346px;
    background:var(--news-bg);border:1px solid var(--panel-edge);border-radius:10px;
  }
  .news-title{position:absolute;left:12px;top:10px;display:flex;align-items:center;gap:8px;font-size:22px;font-weight:300;color:#222}
  .news-item{position:absolute;left:12px;width:254px;font-size:11px;line-height:16px;color:var(--muted)}
  .news-item time{display:block;font-weight:700;font-style:italic;color:#333;margin-bottom:4px}
  .news-divider{position:absolute;left:12px;top:197px;width:252px;height:1px;background:var(--rule)}

  .callout{
    position:absolute;left:666px;top:709px;width:279px;height:110px;
    background:linear-gradient(var(--green-top),var(--green-bottom));
    border:1px solid #5aa51a;border-radius:10px;color:#111;overflow:hidden;
  }
  .callout .row{position:absolute;left:10px;right:8px;display:flex;align-items:center;gap:6px;white-space:nowrap}
  .callout .label{font-size:20px;font-weight:400}
  .callout .value{font-size:13px;font-weight:500}
  .callout .email{font-size:11px}

  .site-footer{position:absolute;left:133px;top:996px;font-size:12px;color:#333}
</style>
</head>
<body>
  <header>
    <a class="brand" href="#">
      <div class="brand-name"><span class="mark"></span>MAPLEWICK HAVEN SUPPLY</div>
      <div class="brand-tagline">Packaging • Printing • Distribution</div>
    </a>
    <nav class="main-nav">
      <a class="active" href="#" style="left:0">HOME</a>
      <a href="#" style="left:106px">ABOUT US</a>
      <a href="#" style="left:213px">SERVICES</a>
      <a href="#" style="left:321px">PRODUCTS</a>
      <a href="#" style="left:429px">FEATURES</a>
      <a href="#" style="left:536px">CONTACT US</a>
    </nav>
  </header>

  <main class="panel">
    <div class="hero" role="img" aria-label="Sandwiches in brown printed cardboard packaging"></div>

    <h1 class="section-title welcome-title">
      <svg class="icon" viewBox="0 0 32 34"><rect x="1" y="3" width="26" height="30" rx="2" fill="#f4f4f4" stroke="#999"/><circle cx="15" cy="18" r="9" fill="#3a7fd0"/><path d="M9 16h12M15 9v18" stroke="#bfe0ff" stroke-width="1.5"/></svg>
      Welcome to&nbsp;<strong>Maplewick Haven supply.</strong>
    </h1>
    <div class="welcome-photo" role="img" aria-label="Folded kraft paper packaging pyramids"></div>
    <p class="welcome-text">
      <span class="lead">Lorem Ipsum is simply dummy text</span> of the printing and typesetting industry. Lorem Ipsum has been the industry's standard dummy text ever since the 1500s, when an unknown printer took a galley of type and scrambled it to make a type specimen book. It has survived not only five centuries, but also the leap into electronic typesetting, remaining essentially unchanged. It was popularised in the 1960s with the release of Letraset sheets containing Lorem Ipsum
      <a class="read-more" href="#">READ MORE</a>
    </p>

    <h2 class="section-title services-title">
      <svg class="icon" viewBox="0 0 32 34"><rect x="2" y="6" width="26" height="26" rx="3" fill="#f2cf2a" stroke="#b8951a"/><circle cx="12" cy="16" r="4" fill="#333"/><circle cx="20" cy="22" r="4" fill="#333"/></svg>
      Services
    </h2>
    <div class="services-rule"></div>

    <section class="service" style="left:20px">
      <h3>Packaging</h3>
      <div class="photo" role="img" aria-label="Open cardboard shipping boxes" style="background:linear-gradient(#c9a47a,#a57b52)"></div>
      <p>Lorem Ipsum is simply dummy text of the printing and typeset-ting industry. Lorem Ipsum has</p>
      <a class="btn" href="#">Read More</a>
    </section>
    <section class="service" style="left:225px">
      <h3>Printing</h3>
      <div class="photo" role="img" aria-label="Colourful printing press rollers" style="background:linear-gradient(100deg,#f0e63a,#3aa0e6 35%,#e63ac8 65%,#f28ad8)"></div>
      <p>Lorem Ipsum is simply dummy text of the printing and typeset-ting industry. Lorem Ipsum has</p>
      <a class="btn" href="#">Read More</a>
    </section>
    <section class="service" style="left:430px">
      <h3>Distribution</h3>
      <div class="photo" role="img" aria-label="Stacked printed shipping cartons" style="background:linear-gradient(90deg,#7f9a74,#d8d1bd 45%,#c7b99b)"></div>
      <p>Lorem Ipsum is simply dummy text of the printing and typeset-ting industry. Lorem Ipsum has</p>
      <a class="btn" href="#">Read More</a>
    </section>

    <aside class="news">
      <h2 class="news-title">
        <svg class="icon" viewBox="0 0 32 34"><rect x="3" y="2" width="24" height="30" rx="2" fill="#fff" stroke="#999"/><rect x="3" y="2" width="24" height="14" fill="#3d8fd6"/><path d="M7 22h16M7 26h12" stroke="#999"/></svg>
        LATEST NEWS
      </h2>
      <article class="news-item" style="top:76px">
        <time>02 05 2012</time>
        Lorem Ipsum is simply dummy text of the printing and typesetting industry. Lorem Ipsum has been the industry's standard dummy text ever since the
        <a class="read-more" href="#">READ MORE</a>
      </article>
      <div class="news-divider"></div>
      <article class="news-item" style="top:233px">
        <time>02 05 2012</time>
        Lorem Ipsum is simply dummy text of the printing and typesetting industry. Lorem Ipsum has been the industry's standard dummy text ever since the
        <a class="read-more" href="#">READ MORE</a>
      </article>
    </aside>

    <aside class="callout">
      <div class="row" style="top:12px">
        <svg width="40" height="30" viewBox="0 0 40 30"><rect x="6" y="12" width="28" height="16" rx="3" fill="#555"/><path d="M2 10q18-12 36 0v4h-8v-4q-10-4-20 0v4H2z" fill="#333"/></svg>
        <span class="label">Call Now:</span><span class="value">(555) 214-0376</span>
      </div>
      <div class="row" style="top:56px">
        <svg width="34" height="28" viewBox="0 0 34 28"><rect x="2" y="4" width="30" height="21" fill="#f4c542" stroke="#a47b12"/><path d="M2 4l15 12 15-12" fill="none" stroke="#a47b12" stroke-width="1.5"/></svg>
        <span class="label">Email:</span><span class="value email">info@maplewickhaven.com</span>
      </div>
    </aside>
  </main>

  <footer class="site-footer">All Right Reserved 2015. Maplewick Haven supply.</footer>
</body>
</html>
```